VFX Company Business Card Design Project

The Kestrel Works is a decentralized Visual Effects Studio servicing the television and feature film industries.
Project Brief:
Take our logo that was previously designed on Pencil Harbor and make a double sided business card.
Requirements:
- Card MUST be double sided.
- Front of card MUST have the yellow part of our logo against the dark grey background.
- Back of card is completely up to the designer.
- Back of card must include the complete company logo.
Please follow these File Preparation guidelines:
http://printnook.ca/infopage?file=filetype_en&s=PrintNook_new&lang=en
Business

```html
<!DOCTYPE html>
<html lang="en">
<head>
<meta charset="utf-8">
<title>The Kestrel Works – Business Card</title>
<link rel="stylesheet" href="https://fonts.googleapis.com/css2?family=PT+Sans:wght@400;700&display=swap">
<style>
  :root {
    --backdrop: #dfe3e6;
    --card-charcoal: #333232;
    --card-edge: #2a2929;
    --brand-yellow: #fcc91c;
    --text-light: #f2f2f2;
    --text-muted: #c9c9c9;
  }
  * { margin: 0; padding: 0; box-sizing: border-box; }
  html, body {
    width: 1200px;
    height: 960px;
    overflow: hidden;
    background: var(--backdrop);
    font-family: "PT Sans", Arial, sans-serif;
  }
  .canvas {
    position: relative;
    width: 1200px;
    height: 960px;
  }
  .card {
    position: absolute;
    left: 232px;
    width: 735px;
    height: 420px;
    background: var(--card-charcoal);
    border: 1px solid var(--card-edge);
    box-shadow: 0 6px 18px rgba(0, 0, 0, 0.18);
    overflow: hidden;
  }
  .card--front { top: 40px; }
  .card--back { top: 500px; }

  /* Front side */
  .holder {
    position: absolute;
    left: 46px;
    top: 58px;
    width: 380px;
    padding-bottom: 10px;
    border-bottom: 3px solid var(--brand-yellow);
    color: var(--text-light);
    white-space: nowrap;
  }
  .holder__name {
    font-size: 34px;
    font-weight: 400;
    letter-spacing: 0.5px;
  }
  .holder__role {
    font-size: 20px;
    margin-left: 4px;
  }
  .contact {
    position: absolute;
    left: 46px;
    top: 150px;
    list-style: none;
    color: var(--text-light);
    font-size: 23px;
    line-height: 34px;
  }
  .contact__label {
    display: inline-block;
    width: 38px;
    color: var(--brand-yellow);
    font-size: 20px;
  }
  .address {
    position: absolute;
    left: 46px;
    top: 268px;
    color: var(--text-light);
    font-size: 23px;
    line-height: 33px;
    font-style: normal;
  }
  .brand-mark {
    position: absolute;
    display: flex;
    align-items: center;
    gap: 14px;
    color: var(--brand-yellow);
    font-weight: 700;
    white-space: nowrap;
  }
  .brand-mark--front {
    right: 42px;
    bottom: 60px;
    font-size: 34px;
  }
  .brand-mark__dot {
    flex: none;
    border-radius: 50%;
    background: var(--brand-yellow);
  }
  .brand-mark--front .brand-mark__dot { width: 34px; height: 34px; }

  /* Back side */
  .brand-mark--back {
    left: 50%;
    top: 50%;
    transform: translate(-50%, -50%);
    font-size: 54px;
  }
  .brand-mark--back .brand-mark__dot { width: 52px; height: 52px; }
</style>
</head>
<body>
<main class="canvas">
  <section class="card card--front" aria-label="Card front">
    <header class="holder">
      <span class="holder__name">MARA QUILL</span>
      <span class="holder__role">Managing Partner</span>
    </header>
    <ul class="contact">
      <li><span class="contact__label">t</span>(555) 014-2290</li>
      <li><span class="contact__label">e</span>name@kestrelworks.com</li>
      <li><span class="contact__label">w</span>www.kestrelworks.com</li>
    </ul>
    <address class="address">
      88 Larkspur Avenue,<br>
      Suite 210, Fenwick,<br>
      Oregon 97000
    </address>
    <div class="brand-mark brand-mark--front">
      <span class="brand-mark__dot"></span>
      <span class="brand-mark__name">The Kestrel Works</span>
    </div>
  </section>

  <section class="card card--back" aria-label="Card back">
    <div class="brand-mark brand-mark--back">
      <span class="brand-mark__dot"></span>
      <span class="brand-mark__name">The Kestrel Works</span>
    </div>
  </section>
</main>
</body>
</html>
```